Feldklang Festival Herbst 2014
Zielgruppe
Lumen Vita veranstaltet KARU MOLEN, Wandeltage im Gaubach. www.wandelfrist-beispiel.de
Yoga, Meditation, Veganes Leben, Vegetarier, Heiler, Esoterik, Spiritualität, Gesundheit, alternative Lebensweisen, Gewaltfreie Kommunikation, Künstler, Musiker,
Als Highlight in diesem Jahr haben wir den weltberühmten japanischen Wissenschaftler Dr. Kenji Tawara zu Gast.
Aufgabenstellung
In Anlehnung an die vergangenen Werbekampagnen soll zu dieser Veranstaltung eingeladen werden. Zu verbessern sind Auffälligkeit und Lesbarkeit.
Plakat in Din 4 und 3
2 leicht unterschiedliche Flyer Din 6,
1. Flyer soll sich am schon vorhandenen Design richten, mit den aktuellen Infos,
2. Flyer soll als Postkarte mit Adressfeld zum Verschicken per Post verwendet werden
Das Foto vom Wasserkristall kann so sicherlich nicht benutz werden, hier würden wir einen grafischen Nachbau empfehlen.
Herauszustellen sind folgende Punkte: Dr. Kenji Tawara, Zirkus Varelli, dass LUMEN VITA dazu einlädt, was LUMEN VITA ist und ganz wichtig, dass der Eintritt frei ist. Das ganze Projekt ist sehr schön auf folgender Pressemitteilung beschrieben
http://www.lebensbote-beispiel.de/meldungen/aktuell/beitrag/fuer-ein-neues-fuereinander-karu-molen-7-wandeltage-im-gaubach/

```html
<!DOCTYPE html>
<html lang="de">
<head>
<meta charset="utf-8">
<title>Wandeltage im Gaubach – Flyer</title>
<link rel="stylesheet" href="https://fonts.googleapis.com/css2?family=Oswald:wght@400;500;600&family=Roboto+Condensed:wght@400;700&family=Cinzel:wght@500&display=swap">
<style>
  :root {
    --orange: #ee6a22;
    --yellow: #f6b01e;
    --ink: #1e1a18;
    --paper: #ffffff;
    --photo-a: #c9a98a;
    --photo-b: #6f8a55;
  }
  * { margin: 0; padding: 0; box-sizing: border-box; }
  html, body { width: 1200px; height: 856px; overflow: hidden; background: var(--paper); }
  .flyer { position: relative; width: 1200px; height: 856px; overflow: hidden; background: var(--orange); font-family: "Oswald", sans-serif; }
  .backdrop { position: absolute; inset: 0; }

  .side-panel { position: absolute; left: 42px; top: 0; width: 412px; height: 856px; background: var(--paper); text-align: center; }
  .side-panel p { white-space: nowrap; }
  .entry-badge { position: absolute; left: 0; top: 18px; width: 276px; height: 118px; background: var(--yellow); border-radius: 0 60px 60px 0; color: var(--paper); font-size: 42px; font-weight: 500; line-height: 118px; padding-left: 20px; text-align: left; white-space: nowrap; z-index: 3; }

  .brand-name { position: absolute; left: 0; right: 0; top: 285px; font-family: "Cinzel", serif; font-size: 54px; line-height: 1; color: var(--ink); letter-spacing: 2px; white-space: nowrap; }
  .mission { position: absolute; left: 0; right: 0; top: 392px; color: var(--orange); font-size: 23px; font-weight: 500; line-height: 40px; }
  .rule { position: absolute; left: 56px; right: 56px; height: 7px; background: var(--yellow); }
  .rule--top { top: 492px; }
  .rule--bottom { top: 668px; }
  .guests { position: absolute; left: 0; right: 0; top: 530px; color: var(--ink); font-size: 26px; font-weight: 500; line-height: 38px; }
  .program { position: absolute; left: 0; right: 0; top: 705px; color: var(--orange); font-size: 20px; font-weight: 500; line-height: 30px; }
  .offer { position: absolute; left: 0; right: 0; top: 778px; font-family: "Roboto Condensed", sans-serif; color: var(--ink); font-size: 20px; line-height: 26px; }

  .web-strip { position: absolute; left: 454px; top: 300px; width: 40px; height: 420px; }
  .web-strip span { position: absolute; left: 50%; top: 50%; transform: translate(-50%, -50%) rotate(-90deg); white-space: nowrap; font-family: "Roboto Condensed", sans-serif; color: var(--paper); font-size: 14px; letter-spacing: 0.5px; }

  .guest-photo { position: absolute; left: 576px; top: 494px; width: 130px; height: 142px; border-radius: 0 26px 0 0; background: linear-gradient(160deg, #9fbf82, #e9e6df 70%); }
  .guest-caption { position: absolute; left: 548px; top: 676px; width: 184px; text-align: center; font-family: "Roboto Condensed", sans-serif; color: var(--ink); font-size: 14.5px; line-height: 18px; }
  .guest-call { position: absolute; left: 548px; top: 730px; width: 184px; text-align: center; color: var(--orange); font-size: 14px; font-weight: 600; line-height: 18px; }

  .event-bar { position: absolute; left: 730px; top: 485px; width: 5px; height: 318px; background: var(--yellow); }
  .event { position: absolute; left: 758px; top: 490px; white-space: nowrap; }
  .event-address { color: var(--orange); font-size: 16px; font-weight: 500; letter-spacing: 0.3px; line-height: 22px; }
  .event-title { margin-top: 10px; color: var(--orange); font-size: 76px; font-weight: 600; line-height: 88px; }
  .event-date { margin-top: 4px; color: var(--ink); font-size: 35px; font-weight: 600; line-height: 42px; }
  .event-hours { margin-top: 2px; font-family: "Roboto Condensed", sans-serif; color: var(--ink); font-size: 16px; line-height: 22px; }

  .host-line { position: absolute; left: 494px; width: 672px; top: 820px; text-align: center; color: var(--paper); font-size: 13px; font-weight: 500; line-height: 20px; white-space: nowrap; }
</style>
</head>
<body>
<main class="flyer">
  <svg class="backdrop" width="1200" height="856" viewBox="0 0 1200 856">
    <defs>
      <linearGradient id="crowdTone" x1="0" y1="0" x2="1" y2="1">
        <stop offset="0" stop-color="#6f8a55"/>
        <stop offset="0.45" stop-color="#c9a98a"/>
        <stop offset="1" stop-color="#8c7a6a"/>
      </linearGradient>
    </defs>
    <path d="M1200 380 C1180 520 1170 640 1200 760 Z" fill="#f6b01e"/>
    <path d="M494 430 Q498 395 540 392 L1150 392 Q1160 392 1160 420 L1160 770 Q1160 804 1125 804 L560 804 Q494 804 494 745 Z" fill="#ffffff"/>
    <path d="M420 0 H1200 V360 C1120 420 1000 448 860 450 C700 450 560 420 470 300 C430 230 415 120 420 0 Z" fill="#f6b01e"/>
    <path d="M440 0 H1200 V340 C1120 400 1000 428 860 430 C710 430 580 402 492 290 C452 225 436 120 440 0 Z" fill="url(#crowdTone)" role="img" aria-label="Gruppenfoto lachender Heilerinnen und Heiler mit erhobenen Armen"/>
  </svg>

  <div class="entry-badge">EINTRITT FREI</div>

  <section class="side-panel">
    <div class="brand-name">KARU MOLEN</div>
    <p class="mission">PLATTFORM FÜR SINNSUCHE, AUSWEGE<br>UND ALTERNATIVEN</p>
    <div class="rule rule--top"></div>
    <p class="guests">DR. KENJI TAWARA<br>DR. MED. LUDGER RAHMSDORF<br>ZIRKUS VARELLI</p>
    <div class="rule rule--bottom"></div>
    <p class="program">AUSSTELLUNG - MUSIK - MARKT<br>KREUZ-QUER TRAUMTHEATER</p>
    <p class="offer">Vorträge, Vorführungen, Workshops<br>sowie Kulinarisches erwartet Sie hier!</p>
  </section>

  <div class="web-strip"><span>www.wandelfrist-beispiel.de &nbsp;•&nbsp; www.karu-molen.eu</span></div>

  <div class="guest-photo" role="img" aria-label="Porträtfoto des Ehrengastes Dr. Kenji Tawara"></div>
  <p class="guest-caption">EHRENGAST<br>DR. KENJI TAWARA</p>
  <p class="guest-call">FRAGEN STELLEN<br>HEILERN BEGEGNEN</p>

  <div class="event-bar"></div>
  <section class="event">
    <p class="event-address">LINDENAUER STR. 12 &nbsp;•&nbsp; 83990 BIRKENFELD</p>
    <h1 class="event-title">WANDELTAGE<br>IM GAUBACH</h1>
    <p class="event-date">21.–22. SEPTEMBER 2014</p>
    <p class="event-hours">SA 10:00 BIS 21:00 UHR &nbsp;|&nbsp; SO 10:00 BIS 19:00 UHR</p>
  </section>

  <p class="host-line">LUMEN VITA® &nbsp;|&nbsp; STATIONÄRES FACHKLINIKUM UND TAGESKLINIK FÜR GEISTIGES HEILEN &nbsp;•&nbsp; HEILERSCHULE</p>
</main>
</body>
</html>
```